Creative UI design for web application

I need a new UI design for my web application. It will be used by small and micro business owners to plan & implement growth tactics.

I've attached the current design (which I'm open to be changed) - but in particular I need to design the centre of the screen, where the work actually happens.

There needs to be place for a title (YOUR BUSINESS) and description (say 1-2 paragraphs of text) - and am happy to include icons or imagery where makes sense. It may make sense for the user to be able to upload their business logo and name, for example.

This screen will be used by the business owner to understand the real value they offer potential customers and their point of difference - why they exist and why potential customers should care.

They'll use the information they put into this screen to plan things like their messaging.

Following that, there needs to be 2 sections in the dashboard.

The first section is titled "WHO YOU ARE"

The first section will include a number of boxes that the user can input information into, as follows:

- Logo
- Business name
- Business tag line
- Business vision
- Business bio
- Brand colours (these should end up as swatches based on the colour code they enter) - the colour code for each colour swatch should also be visible.
- Key competitors
- SWOT analysis (boxes to enter their strengths, weaknesses, opportunities and threats).

The second section is titled "WHY YOU EXIST"

The second section will include a number of boxes that the user can input information (text) into, as follows:

- Who are your ideal customers?
- What problem are you trying to solve for them?
- What pain points will this remove for them?
- How do you solve it?
- How else could this problem be solved?
- Who offers these other solutions?
- Why is your solution better?
- How much does your solution cost?
- What value are you providing to justify this cost?
- How will this make their life/job easier/better?

They should be able to write a decent amount of information in the boxes.

There should ideally be a place for a description for each of these text fields (for both section 1 & 2) as well so I can give them a little bit more direction around what to put in the box. Alternatively there could be a little icon (say a question mark or "i") that they could click on to view instructions. The instructions will be around 2-4 sentences long for each text field.

You have 2 options:

a) This all needs to appear on the one screen, and the navigation needs to be visible (as per the example attached but feel free to recreate this navigation)

Note: the page can scroll below the fold - but please provide the design for the full length of the page.

b) Potentially the 2 sections could actually be in 2 different items in the menu - YOUR BUSINESS and YOUR VALUE (which would sit next to YOUR BUSINESS and before YOUR CUSTOMER in the screenshot provided). feel free to design them as 2 separate screens if you prefer.

I have attached a screenshot of the app as it stands today (screen shot 2017) which would still exist in the new design but under a different section (the learn section from the plan2 mockup attached)

I have mocked up how this new screen could look if broken into 2 and that's also attached. If you can make this come to life - and look more engaging that would be helpful! :)

Target Market(s)

Small and micro business owners

Industry/Entity Type

Marketing

Number of Pages Required

1 page

Font styles to use
Sans Serif
Other font styles liked:
• Montserrat

Colors
87cfc6
d2a4cc
ffffff
85cae6
e8e8e8
5c5c5c

Requirements
Must have
• Use of my brand colours: #cc8eb2, #76d6c8, #68c7ff as well as white and #595959. Must be visually pleasing / engaging, designed for desktop (as it's a desktop application), really easy to use / navigate.
• Use font Montserrat light & Montserrat Regular or Bold. Mostly should be Montserrat light.
Nice to have
• Would be nice to see how this would look on mobile (as the application is responsive) but this is not mandatory.
Should not have
• Should not look too corporate or dry.

```html
<!DOCTYPE html>
<html lang="en">
<head>
<meta charset="utf-8">
<title>Bloomwise – Your Business</title>
<link href="https://fonts.googleapis.com/css2?family=Montserrat:wght@300;400;500&display=swap" rel="stylesheet">
<style>
  :root {
    --ink: #5c5c5c;
    --ink-soft: #8a8a8a;
    --bar-dark: #3b3b3b;
    --pink: #d2a4cc;
    --pink-deep: #cc8eb2;
    --teal: #87cfc6;
    --panel: #f7f7f7;
    --panel-line: #ececec;
    --box: #e8e8e8;
    --white: #ffffff;
    --hero-bg: #fafafa;
  }
  * { box-sizing: border-box; margin: 0; padding: 0; }
  html, body { width: 1200px; height: 3523px; overflow: hidden; }
  body {
    position: relative;
    background: var(--white);
    font-family: "Montserrat", sans-serif;
    font-weight: 300;
    color: var(--ink);
  }
  .abs { position: absolute; }

  /* top navigation */
  .topbar { left: 0; top: 0; width: 1200px; height: 40px; background: var(--bar-dark); }
  .brand { left: 40px; top: 0; height: 40px; line-height: 40px; color: var(--white); font-size: 15px; font-weight: 400; letter-spacing: .5px; }
  .main-tab { top: 0; height: 40px; line-height: 40px; color: var(--white); font-size: 12px; font-weight: 400; text-align: center; }
  .main-tab.is-active { background: var(--teal); }
  .account-link { top: 0; height: 40px; display: flex; align-items: center; gap: 8px; color: var(--white); font-size: 11px; font-weight: 400; }

  /* section navigation */
  .subbar { left: 0; top: 40px; width: 1200px; height: 45px; background: var(--pink); }
  .sub-tab { top: 40px; height: 45px; line-height: 45px; color: var(--white); font-size: 13px; font-weight: 400; transform: translateX(-50%); white-space: nowrap; }
  .sub-tab.is-active { color: var(--ink); }

  /* business profile */
  .profile { left: 0; top: 85px; width: 1200px; height: 585px; background: var(--hero-bg); }
  .avatar { left: 140px; top: 140px; width: 100px; height: 100px; border-radius: 50%; background: radial-gradient(circle at 50% 40%, #e8b9a0, #b4633f 75%); border: 3px solid #fff; box-shadow: 0 0 0 1px #ddd; }
  .biz-name { left: 272px; top: 147px; font-size: 21px; font-weight: 400; letter-spacing: .5px; color: var(--ink); }
  .contact { top: 188px; display: flex; align-items: center; gap: 8px; font-size: 11px; font-weight: 400; }
  .biz-summary { left: 272px; top: 222px; width: 456px; font-size: 10.5px; line-height: 22px; color: var(--ink-soft); }
  .social { left: 272px; top: 310px; display: flex; gap: 4px; }
  .social span { width: 40px; height: 40px; border-radius: 6px; display: block; }
  .hero-photo { left: 756px; top: 136px; width: 317px; height: 233px; background: linear-gradient(120deg, #c99a84 0%, #e9cbb8 45%, #a8735e 100%); }
  .intro { left: 129px; width: 940px; font-size: 10.5px; line-height: 28px; color: var(--ink-soft); text-align: center; }

  /* section titles */
  .section-title { left: 0; width: 1200px; text-align: center; font-size: 30px; font-weight: 400; color: var(--ink); }

  /* input cards */
  .card { background: var(--panel); }
  .card-head { height: 33px; line-height: 33px; padding-left: 14px; color: var(--white); font-size: 13px; font-weight: 400; }
  .card.who .card-head { background: var(--pink); }
  .card.why .card-head { background: var(--teal); }
  .card-body { padding: 14px; font-size: 10px; line-height: 20px; color: var(--ink-soft); }

  .swatches { position: absolute; left: 14px; bottom: 20px; display: flex; gap: 2px; }
  .swatch { width: 29px; }
  .swatch i { display: block; width: 29px; height: 31px; }
  .swatch small { display: block; font-size: 5px; margin-top: 2px; color: var(--ink-soft); font-style: normal; }

  .swot-label { top: 1573px; font-size: 12px; font-weight: 400; color: var(--ink); letter-spacing: .5px; }
  .swot-box { top: 1601px; height: 162px; background: var(--box); padding: 16px 18px; font-size: 10px; line-height: 20px; color: var(--ink); }

  .save { left: 502px; top: 3367px; width: 195px; height: 40px; background: var(--pink); color: var(--white); border: 0; font-family: "Montserrat", sans-serif; font-size: 13px; font-weight: 400; letter-spacing: .5px; }

  .footer { left: 0; top: 3461px; width: 1200px; height: 62px; background: var(--bar-dark); color: #cfcfcf; font-size: 11px; }
  .footer .copy { position: absolute; left: 0; width: 1200px; top: 0; line-height: 62px; text-align: center; }
  .footer .code { position: absolute; right: 28px; top: 0; line-height: 62px; }
</style>
</head>
<body>

<header>
  <div class="abs topbar"></div>
  <div class="abs brand">BLOOMWISE</div>
  <div class="abs main-tab is-active" style="left:242px;width:129px;">Plan</div>
  <div class="abs main-tab" style="left:395px;width:70px;">Learn</div>
  <div class="abs main-tab" style="left:520px;width:90px;">Remember</div>
  <div class="abs account-link" style="left:927px;">
    <svg width="14" height="14" viewBox="0 0 14 14"><circle cx="7" cy="7" r="7" fill="var(--teal)"/><circle cx="7" cy="5.4" r="2.3" fill="#fff"/><path d="M3 11.5c.8-2 2.3-3 4-3s3.2 1 4 3" fill="#fff"/></svg>
    My Profile
  </div>
  <div class="abs account-link" style="left:1040px;">
    <svg width="14" height="14" viewBox="0 0 14 14"><path d="M6 2H2v10h4" stroke="var(--teal)" stroke-width="1.6" fill="none"/><path d="M5 7h8M10 4l3 3-3 3" stroke="var(--teal)" stroke-width="1.6" fill="none"/></svg>
    Log Out
  </div>

  <nav>
    <div class="abs subbar"></div>
    <div class="abs sub-tab is-active" style="left:312px;">Your Business</div>
    <div class="abs sub-tab" style="left:500px;">Your products</div>
    <div class="abs sub-tab" style="left:697px;">Your Customers</div>
    <div class="abs sub-tab" style="left:866px;">Your Goals</div>
    <div class="abs sub-tab" style="left:1024px;">Your Plan</div>
  </nav>
</header>

<section>
  <div class="abs profile"></div>
  <div class="abs avatar" role="img" aria-label="Portrait photo of the business owner"></div>
  <h1 class="abs biz-name">MARA QUILL MAKEUP</h1>
  <div class="abs contact" style="left:272px;">
    <svg width="12" height="9" viewBox="0 0 12 9"><rect width="12" height="9" rx="1" fill="var(--ink)"/><path d="M0.5 1l5.5 4 5.5-4" stroke="#fff" fill="none"/></svg>
    info@maraquill.com
  </div>
  <div class="abs contact" style="left:439px;">
    <svg width="11" height="11" viewBox="0 0 11 11"><path d="M2.2 0.5l2 2.3-1 1.3c.7 1.5 1.9 2.7 3.4 3.4l1.3-1 2.3 2-1 2C4.5 10.3.7 6.5.2 1.5z" fill="var(--ink)"/></svg>
    1800 555 019
  </div>
  <p class="abs biz-summary">We help local clients look and feel their best for weddings, events and photo shoots, with friendly service and products chosen for every skin type and style.</p>
  <div class="abs social" aria-label="Social links">
    <span style="background:#7a8fc4"></span>
    <span style="background:#68c7ff"></span>
    <span style="background:#f2a35c"></span>
    <span style="background:#d9745f"></span>
  </div>
  <div class="abs hero-photo" role="img" aria-label="Photo of a makeup artist applying makeup to a client"></div>

  <p class="abs intro" style="top:422px;">This page helps you describe your business in your own words. Start with who you are, then explain why you exist and what makes you different. Take your time with each box, because the answers you give here will shape your messaging, your offers and the way you talk to the customers you most want to reach and keep over time.</p>
  <p class="abs intro" style="top:535px;">Come back to these answers often. As your business grows, your customers, competitors and goals will change, and so should this page. Short, honest notes are better than long ones, so write the way you speak and update anything that no longer feels true to the work you do and the people you serve every day.</p>
</section>

<section>
  <h2 class="abs section-title" style="top:712px;">Who You Are</h2>

  <div class="abs card who" style="left:68px;top:787px;width:510px;height:117px;">
    <div class="card-head">Business Tag Line</div>
    <div class="card-body">Write a short answer here so your plan stays clear and focused.</div>
  </div>
  <div class="abs card who" style="left:622px;top:787px;width:521px;height:117px;">
    <div class="card-head">Business Vision</div>
    <div class="card-body">Write a short answer here so your plan stays clear and focused.</div>
  </div>
  <div class="abs card who" style="left:68px;top:935px;width:1075px;height:232px;">
    <div class="card-head">Business Bio</div>
    <div class="card-body">Write a short answer here so your plan stays clear and focused.</div>
  </div>
  <div class="abs card who" style="left:68px;top:1197px;width:510px;height:223px;">
    <div class="card-head">Brand colours</div>
    <div class="card-body">Write a short answer here so your plan stays clear and focused.</div>
    <div class="swatches">
      <div class="swatch"><i style="background:#f7941d"></i><small>#F7941D</small></div>
      <div class="swatch"><i style="background:#f26522"></i><small>#F26522</small></div>
      <div class="swatch"><i style="background:#e8541c"></i><small>#E8541C</small></div>
      <div class="swatch"><i style="background:#d9531e"></i><small>#D9531E</small></div>
      <div class="swatch"><i style="background:#c0450f"></i><small>#C0450F</small></div>
      <div class="swatch"><i style="background:#6b3009"></i><small>#6B3009</small></div>
    </div>
  </div>
  <div class="abs card who" style="left:622px;top:1197px;width:521px;height:223px;">
    <div class="card-head">Key competitors</div>
    <div class="card-body">Write a short answer here so your plan stays clear and focused.</div>
  </div>

  <div class="abs card who" style="left:68px;top:1465px;width:1075px;height:336px;">
    <div class="card-head">SWOT Analysis</div>
    <div class="card-body">Write a short answer here so your plan stays clear and focused.</div>
  </div>
  <div class="abs swot-label" style="left:92px;">STRENGTHS</div>
  <div class="abs swot-label" style="left:350px;">WEAKNESSES</div>
  <div class="abs swot-label" style="left:603px;">OPPORTUNITIES</div>
  <div class="abs swot-label" style="left:866px;">THREATS</div>
  <div class="abs swot-box" style="left:92px;width:239px;">List the points that matter most to your business today.</div>
  <div class="abs swot-box" style="left:350px;width:244px;">List the points that matter most to your business today.</div>
  <div class="abs swot-box" style="left:603px;width:245px;">List the points that matter most to your business today.</div>
  <div class="abs swot-box" style="left:866px;width:247px;">List the points that matter most to your business today.</div>
</section>

<section>
  <h2 class="abs section-title" style="top:1867px;">Why You Exist</h2>

  <div class="abs card why" style="left:63px;top:1960px;width:515px;height:118px;">
    <div class="card-head">Who are your ideal customers?</div>
    <div class="card-body">Write a short answer here so your plan stays clear and focused.</div>
  </div>
  <div class="abs card why" style="left:622px;top:1960px;width:519px;height:118px;">
    <div class="card-head">What problem are you trying to solve for them?</div>
    <div class="card-body">Write a short answer here so your plan stays clear and focused.</div>
  </div>
  <div class="abs card why" style="left:63px;top:2116px;width:1078px;height:232px;">
    <div class="card-head">What pain points will this remove for them?</div>
    <div class="card-body">Write a short answer here so your plan stays clear and focused.</div>
  </div>
  <div class="abs card why" style="left:63px;top:2378px;width:515px;height:224px;">
    <div class="card-head">How do you solve it?</div>
    <div class="card-body">Write a short answer here so your plan stays clear and focused.</div>
  </div>
  <div class="abs card why" style="left:622px;top:2378px;width:519px;height:224px;">
    <div class="card-head">How else could this problem be solved?</div>
    <div class="card-body">Write a short answer here so your plan stays clear and focused.</div>
  </div>
  <div class="abs card why" style="left:63px;top:2646px;width:1078px;height:219px;">
    <div class="card-head">Who offers these other solutions?</div>
    <div class="card-body">Write a short answer here so your plan stays clear and focused.</div>
  </div>
  <div class="abs card why" style="left:63px;top:2914px;width:515px;height:223px;">
    <div class="card-head">Why is your solution better?</div>
    <div class="card-body">Write a short answer here so your plan stays clear and focused.</div>
  </div>
  <div class="abs card why" style="left:622px;top:2914px;width:519px;height:223px;">
    <div class="card-head">How much does your solution cost?</div>
    <div class="card-body">Write a short answer here so your plan stays clear and focused.</div>
  </div>
  <div class="abs card why" style="left:63px;top:3179px;width:515px;height:120px;">
    <div class="card-head">What value are you providing to justify this cost?</div>
    <div class="card-body">Write a short answer here so your plan stays clear and focused.</div>
  </div>
  <div class="abs card why" style="left:622px;top:3179px;width:519px;height:120px;">
    <div class="card-head">How will this make their life/job easier/better?</div>
    <div class="card-body">Write a short answer here so your plan stays clear and focused.</div>
  </div>

  <button class="abs save" type="button">SAVE CHANGES</button>
</section>

<footer class="abs footer">
  <div class="copy">© 2017 Bloomwise. All Rights Reserved.</div>
  <div class="code">C12</div>
</footer>

</body>
</html>
```